Professional & attention grabbing.

A business card design, front and back. I already have a logo I will attach, but I am open to something new as well.
Things to include:
Name:
Title:
Phone:
Email:
Wanting something that is professional but attention grabbing.
Also we do a lot of work using drones on natural gas pipelines (leading the future)if you want to include any of that. I'm open to ideas.
Target Market(s)
Natural gas transmission industry / greenhouse gas mitigation industry
Industry/Entity Type
Business
Colors
Designer to choose colors to be used in the design.
Look and feel
Each slider illustrates characteristics of the customer's brand and the style your logo design should communicate.

```html
<!DOCTYPE html>
<html lang="en">
<head>
<meta charset="utf-8">
<title>KV Field Inspections – Business Card</title>
<link rel="stylesheet" href="https://fonts.googleapis.com/css2?family=Arimo:wght@400;700&display=swap">
<style>
  :root {
    --bg: #e8e6e3;
    --card: #ffffff;
    --red: #be1f24;
    --charcoal: #39393b;
    --ink: #111111;
    --rule: #c9c9c9;
  }
  * { margin: 0; padding: 0; box-sizing: border-box; }
  html, body {
    width: 1200px; height: 1135px; overflow: hidden;
    background: var(--bg);
    font-family: "Arimo", Arial, sans-serif;
  }
  .card {
    position: absolute; left: 234px;
    width: 680px; height: 405px;
    background: var(--card);
    overflow: hidden;
    box-shadow: 0 10px 24px rgba(0,0,0,.25);
  }
  .card--front { top: 90px; }
  .card--back { top: 625px; }
  .card__bands { position: absolute; inset: 0; width: 680px; height: 405px; }
  .brand {
    position: absolute; display: flex; align-items: center; gap: 10px;
    color: var(--charcoal); font-weight: 700; font-size: 28px; letter-spacing: -.2px;
  }
  .brand__square { width: 26px; height: 26px; background: var(--red); }
  .card--front .brand { left: 32px; top: 50px; }
  .card--back .brand { left: 42px; top: 175px; }
  .identity { position: absolute; left: 457px; top: 42px; color: var(--ink); }
  .identity__name { font-size: 28px; font-weight: 700; line-height: 1.1; }
  .identity__title { font-size: 16px; line-height: 1.2; }
  .contact { position: absolute; left: 457px; top: 183px; list-style: none; color: var(--ink); font-size: 15px; }
  .contact li { display: flex; align-items: center; gap: 9px; height: 28px; margin-bottom: 10px; }
  .contact svg { width: 18px; height: 18px; }
  .back-rule { position: absolute; left: 297px; right: 0; top: 134px; height: 1px; background: var(--rule); }
</style>
</head>
<body>

<section class="card card--front">
  <svg class="card__bands" viewBox="0 0 680 405" aria-hidden="true">
    <path fill="var(--red)" d="M0,225 C200,165 420,335 680,265 V405 H0 Z"/>
    <path fill="var(--charcoal)" d="M0,265 C220,215 430,395 680,335 V405 H0 Z"/>
  </svg>
  <div class="brand"><span class="brand__square"></span>KV Field Inspections</div>
  <div class="identity">
    <p class="identity__name">Your Name</p>
    <p class="identity__title">Title</p>
  </div>
  <ul class="contact">
    <li>
      <svg viewBox="0 0 18 18" aria-hidden="true"><rect width="18" height="18" rx="4" fill="var(--ink)"/><path fill="#fff" d="M6 4.5l1.6 2.4-1 1.2c.6 1.4 1.6 2.4 3 3l1.2-1 2.4 1.6-.8 1.8c-3.8-.2-7.2-3.6-7.4-7.4z"/></svg>
      <span>555 014 2290</span>
    </li>
    <li>
      <svg viewBox="0 0 18 18" aria-hidden="true"><rect width="18" height="18" rx="4" fill="var(--ink)"/><rect x="4" y="5.5" width="10" height="7" rx="1" fill="#fff"/></svg>
      <span>name@kvfield.com</span>
    </li>
  </ul>
</section>

<section class="card card--back">
  <div class="back-rule"></div>
  <svg class="card__bands" viewBox="0 0 680 405" aria-hidden="true">
    <path fill="var(--red)" d="M0,300 C220,255 440,350 680,280 V405 H0 Z"/>
    <path fill="var(--charcoal)" d="M0,345 C240,300 460,390 680,320 V405 H0 Z"/>
  </svg>
  <div class="brand"><span class="brand__square"></span>KV Field Inspections</div>
</section>

</body>
</html>
```